Tidewell Comforts, a portable luxury restroom trailer company needs a landing page

We need a landing page for a luxury portable restroom trailer company. This should be modern, and simple - use any combination of Pantone colors: Warm Gray 1C, Black 7C, 7529c, 873C, 8003C

We rent these trailers for special events like weddings, private parties, festivals, family reunions, team building, wine tastings, beer tastings, food truck round-ups, etc.

An idea of the landing page is in the files below. Please use stock photography and placeholder text for now. The winning design will be given final content.

Requirements
Must have
• Multiple "Get Quote" buttons or a place for them to type in type of rental, how many people etc

```html
<!DOCTYPE html>
<html lang="en">
<head>
<meta charset="utf-8">
<title>Tidewell Comforts – Luxury Restroom Trailers</title>
<link href="https://fonts.googleapis.com/css2?family=Arimo:wght@400;700&family=Montserrat:wght@400;500;600&display=swap" rel="stylesheet">
<style>
:root{
  --black:#231f1c;
  --black-7c:#3d3935;
  --gold:#8c7a4b;
  --gold-light:#a8925c;
  --bronze:#7c6a55;
  --bronze-deep:#5e4f40;
  --taupe:#b7ab9c;
  --warm-gray:#d7d2cb;
  --text:#3d3935;
  --muted:#5a544e;
  --white:#fff;
}
*{margin:0;padding:0;box-sizing:border-box}
html,body{width:1200px;height:3628px;overflow:hidden}
body{position:relative;font-family:"Arimo",Arial,sans-serif;color:var(--text);background:var(--white)}
.abs{position:absolute}
.btn{position:absolute;display:flex;align-items:center;justify-content:center;border-radius:22px;color:var(--white);font-weight:700;font-size:14px;text-transform:uppercase}
.btn-gold{background:var(--gold)}
.btn-dark{background:var(--black-7c)}

/* header */
.site-header{left:0;top:0;width:1200px;height:111px;background:var(--black)}
.brand{left:108px;top:34px;color:var(--white);font-weight:700;font-size:21px;line-height:25px;text-transform:uppercase}
.nav a{position:absolute;top:41px;color:var(--white);font-size:14px;font-weight:700;text-decoration:none}
.nav a.active{color:var(--gold-light);border-bottom:2px solid var(--gold-light);padding-bottom:5px}
.quote{left:876px;top:25px;width:212px;height:51px;border-radius:26px;font-size:14px}

/* hero */
.hero{left:0;top:111px;width:1200px;height:549px;background:linear-gradient(90deg,#4d6b4a 0%,#2f5fb0 25%,#7a8a6a 50%,#b8c3c8 62%,#1f7ad6 80%,#2a88e0 100%)}
.hero-band{left:300px;top:452px;width:600px;height:170px;background:rgba(35,31,28,.6)}
.hero-title{left:0;top:468px;width:1200px;text-align:center;color:var(--white);font-size:51px;font-weight:700;text-transform:uppercase}
.hero-cta{left:525px;top:543px;width:150px;height:42px}
.hero-arrow{width:40px;height:40px;border-radius:50%;background:rgba(255,255,255,.35)}

/* events */
.section-title{font-size:37px;font-weight:700;text-transform:uppercase}
.events-intro{left:477px;top:741px;width:600px;font-size:14px;line-height:21px;color:var(--muted)}
.event-card{top:841px;width:313px;height:290px}
.event-photo{position:absolute;left:0;top:0;width:313px;height:229px;border-top-right-radius:44px}
.event-label{position:absolute;left:0;top:229px;width:313px;height:61px;background:var(--warm-gray);display:flex;align-items:center;justify-content:space-between;padding:0 22px;font-size:22px;font-weight:700;color:var(--text)}
.event-date{position:absolute;left:16px;top:-24px;width:57px;height:59px;background:var(--gold);color:var(--white);font-weight:700;font-size:18px;line-height:20px;text-align:center;padding-top:8px}

/* products */
.products{left:0;top:1288px;width:1200px;height:1265px;background:linear-gradient(135deg,var(--bronze) 0%,var(--bronze-deep) 45%,var(--bronze) 70%,var(--bronze-deep) 100%)}
.product-row{left:111px;width:977px;height:297px;background:var(--white)}
.product-copy{position:absolute;width:420px}
.product-copy h3{font-size:26px;line-height:34px;font-weight:700;color:var(--text)}
.product-copy p{margin-top:12px;width:412px;font-size:14px;line-height:21px;color:var(--muted)}
.product-photo{position:absolute;top:0;width:489px;height:297px}

/* contact */
.contact-panel{left:111px;top:2639px;width:392px;height:329px;background:var(--bronze)}
.contact-frame{left:773px;top:2639px;width:315px;height:329px;border:4px solid var(--gold)}
.contact-kicker{right:806px;top:2717px;color:var(--white);font-size:18px;font-weight:700;text-align:right}
.contact-slogan{right:806px;top:2760px;color:var(--white);font-size:38px;line-height:46px;font-weight:700;text-align:right}
.form-card{left:432px;top:2681px;width:616px;height:401px;background:var(--white);box-shadow:0 4px 18px rgba(0,0,0,.15)}
.form-title{left:432px;top:2718px;width:616px;text-align:center;font-size:28px;font-weight:700;color:var(--black)}
.field{position:absolute;width:250px;height:34px;border-bottom:1px solid #ccc;font-family:"Montserrat",sans-serif;font-size:12px;color:#777;padding-top:6px}
.field.select::after{content:"";position:absolute;right:8px;top:11px;width:5px;height:5px;border-right:1px solid #777;border-bottom:1px solid #777;transform:rotate(45deg)}

/* footer */
.footer{left:0;top:3185px;width:1200px;height:443px;background:var(--black)}
.footer-brand{left:110px;top:3312px;color:var(--white);font-family:"Montserrat",sans-serif;font-weight:600;font-size:40px;line-height:44px;text-transform:uppercase;letter-spacing:1px}
.social{position:absolute;top:3419px;width:30px;height:30px;border:1.5px solid var(--white);border-radius:50%;display:flex;align-items:center;justify-content:center}
.footer-col{font-family:"Montserrat",sans-serif;color:var(--white)}
.footer-col h4{font-size:18px;font-weight:600;margin-bottom:18px}
.footer-col li{list-style:none;font-size:15px;line-height:26px}
.contact-item{position:absolute;left:591px;font-family:"Montserrat",sans-serif;color:var(--white);font-size:14px;line-height:20px}
.footer-rule{left:111px;top:3519px;width:977px;height:1px;background:#4a4540}
.copyright{left:0;top:3555px;width:1200px;text-align:center;font-family:"Montserrat",sans-serif;color:var(--white);font-size:15px}
.copyright u{text-underline-offset:3px}
</style>
</head>
<body>

<header class="abs site-header">
  <div class="abs brand">Tidewell<br>Comforts</div>
  <nav class="nav">
    <a class="active" style="left:508px">HOME</a>
    <a style="left:585px">EVENT</a>
    <a style="left:667px">PRODUCT</a>
    <a style="left:771px">CONTACT</a>
  </nav>
  <div class="btn btn-gold quote">Request a quote</div>
</header>

<section class="abs hero" role="img" aria-label="Collage of portable restroom units and restroom trailers outdoors"></section>
<div class="abs hero-band"></div>
<div class="abs hero-arrow" style="left:71px;top:346px"></div>
<div class="abs hero-arrow" style="left:1087px;top:346px"></div>
<svg class="abs" style="left:86px;top:360px" width="12" height="12"><path d="M8 1 3 6l5 5" fill="none" stroke="#3d3935" stroke-width="1.5"/></svg>
<svg class="abs" style="left:1102px;top:360px" width="12" height="12"><path d="M4 1l5 5-5 5" fill="none" stroke="#3d3935" stroke-width="1.5"/></svg>
<h1 class="abs hero-title">Tidewell Comforts</h1>
<div class="btn btn-gold hero-cta">Get started</div>

<h2 class="abs section-title" style="left:110px;top:738px;color:var(--black)">Our Events</h2>
<p class="abs events-intro">Lorem ipsum dolor sit amet, consectetur adipiscing elit, sed do eiusmod tempor incididunt ut labore et dolore magna aliqua. Ut enim ad minim veniam, quis nostrud exercitatio</p>

<article class="abs event-card" style="left:111px">
  <div class="event-photo" role="img" aria-label="Wedding couple leaving the ceremony" style="background:linear-gradient(135deg,#1e1e1e,#6d6d6d 60%,#d9d9d9)"></div>
  <div class="event-date">MON<br>16</div>
  <div class="event-label">Weddings<svg width="18" height="18" viewBox="0 0 18 18"><path d="M2 9h12M9 3l6 6-6 6" fill="none" stroke="#8c7a4b" stroke-width="3"/></svg></div>
</article>
<article class="abs event-card" style="left:444px">
  <div class="event-photo" role="img" aria-label="Friends celebrating at a private party" style="background:linear-gradient(135deg,#6a1f5c,#c2386a 50%,#2a5a3a)"></div>
  <div class="event-date">MON<br>16</div>
  <div class="event-label">Private Parties<svg width="18" height="18" viewBox="0 0 18 18"><path d="M2 9h12M9 3l6 6-6 6" fill="none" stroke="#8c7a4b" stroke-width="3"/></svg></div>
</article>
<article class="abs event-card" style="left:776px">
  <div class="event-photo" role="img" aria-label="Family gathered at a reunion table" style="background:linear-gradient(135deg,#3c3a30,#7a6a55 55%,#c9b9a8)"></div>
  <div class="event-date">MON<br>16</div>
  <div class="event-label">Family Reunions<svg width="18" height="18" viewBox="0 0 18 18"><path d="M2 9h12M9 3l6 6-6 6" fill="none" stroke="#8c7a4b" stroke-width="3"/></svg></div>
</article>
<div class="btn btn-gold" style="left:498px;top:1162px;width:203px;height:42px">View more events</div>

<section class="abs products" role="img" aria-label="Flowing fabric background"></section>
<h2 class="abs section-title" style="left:0;top:1368px;width:1200px;text-align:center;color:#fff">Our Product</h2>

<article class="abs product-row" style="top:1443px">
  <div class="product-copy" style="left:32px;top:25px">
    <h3>Lorem ipsum dolor sit amet, consectetur adipiscing</h3>
    <p>Lorem ipsum dolor sit amet, consectetur adipiscing elit, sed do eiusmod tempor incididunt ut labore et dolore magna aliqua. Ut enim ad minim veniam, quis nostrud exercitation ullamco laboris nisi ut aliquip ex ea commodo consequat. Duis aute irure dolor in reprehenderit in voluptate velit esse cillum dolore</p>
  </div>
  <div class="btn btn-gold" style="left:33px;top:228px;width:150px;height:42px">Learn more</div>
  <div class="btn btn-dark" style="left:196px;top:228px;width:150px;height:42px">Book now</div>
  <div class="product-photo" role="img" aria-label="Row of portable restrooms beside a road under a cloudy sky" style="left:488px;background:linear-gradient(180deg,#8ea6bf 0%,#c9d4de 45%,#6c7a4e 70%,#4b5560 100%)"></div>
</article>

<article class="abs product-row" style="top:1761px">
  <div class="product-photo" role="img" aria-label="Restroom trailer parked on grass" style="left:0;background:linear-gradient(180deg,#4f8fd0 0%,#a9c6dc 35%,#d8d8d0 55%,#6e9a4a 80%,#a9a89a 100%)"></div>
  <div class="product-copy" style="left:530px;top:25px">
    <h3>Lorem ipsum dolor sit amet, consectetur adipiscing</h3>
    <p>Lorem ipsum dolor sit amet, consectetur adipiscing elit, sed do eiusmod tempor incididunt ut labore et dolore magna aliqua. Ut enim ad minim veniam, quis nostrud exercitation ullamco laboris nisi ut aliquip ex ea commodo consequat. Duis aute irure dolor in reprehenderit in voluptate velit esse cillum dolore</p>
  </div>
  <div class="btn btn-gold" style="left:531px;top:228px;width:150px;height:42px">Learn more</div>
  <div class="btn btn-dark" style="left:694px;top:228px;width:150px;height:42px">Book now</div>
</article>

<article class="abs product-row" style="top:2078px">
  <div class="product-copy" style="left:32px;top:25px">
    <h3>Lorem ipsum dolor sit amet, consectetur adipiscing</h3>
    <p>Lorem ipsum dolor sit amet, consectetur adipiscing elit, sed do eiusmod tempor incididunt ut labore et dolore magna aliqua. Ut enim ad minim veniam, quis nostrud exercitation ullamco laboris nisi ut aliquip ex ea commodo consequat. Duis aute irure dolor in reprehenderit in voluptate velit esse cillum dolore</p>
  </div>
  <div class="btn btn-gold" style="left:33px;top:228px;width:150px;height:42px">Learn more</div>
  <div class="btn btn-dark" style="left:196px;top:228px;width:150px;height:42px">Book now</div>
  <div class="product-photo" role="img" aria-label="Restroom trailer at a construction site" style="left:488px;background:linear-gradient(180deg,#3f8fd6 0%,#9cc6e6 35%,#c58a52 60%,#d8c6a8 100%)"></div>
</article>
<div class="btn btn-gold" style="left:486px;top:2426px;width:228px;height:42px">View more products</div>

<div class="abs contact-panel"></div>
<div class="abs contact-frame"></div>
<div class="abs contact-kicker">CONTACT US</div>
<div class="abs contact-slogan">LET’S GO<br>GOOD<br>TOGETHER</div>

<form class="abs form-card" aria-label="Quote request form"></form>
<h2 class="abs form-title">SEND US A MESSAGE</h2>
<div class="field" style="left:476px;top:2780px">Name</div>
<div class="field" style="left:749px;top:2780px">Email address</div>
<div class="field" style="left:476px;top:2833px">Phone</div>
<div class="field select" style="left:749px;top:2833px">Type of event</div>
<div class="field select" style="left:476px;top:2880px">Type of project you’re interest in?</div>
<div class="field select" style="left:749px;top:2880px">When do you need it?</div>
<div class="field select" style="left:476px;top:2938px">For how long?</div>
<div class="field select" style="left:749px;top:2938px">Where?</div>
<div class="btn btn-gold" style="left:665px;top:2995px;width:150px;height:42px">Submit now</div>

<footer class="abs footer"></footer>
<svg class="abs" style="left:520px;top:3185px" width="160" height="42" viewBox="0 0 160 42">
  <path d="M0 0h160v0c-40 0-70 12-80 42C70 12 40 0 0 0z" fill="#fff"/>
</svg>
<div class="abs footer-brand">Tidewell<br>Comforts</div>
<div class="social" style="left:115px" aria-label="Share"><svg width="14" height="14" viewBox="0 0 14 14"><circle cx="3" cy="7" r="2" fill="#fff"/><circle cx="11" cy="3" r="2" fill="#fff"/><circle cx="11" cy="11" r="2" fill="#fff"/><path d="M3 7l8-4M3 7l8 4" stroke="#fff" stroke-width="1.2"/></svg></div>
<div class="social" style="left:150px" aria-label="Email"><svg width="14" height="10" viewBox="0 0 14 10"><rect x=".6" y=".6" width="12.8" height="8.8" fill="none" stroke="#fff" stroke-width="1.2"/><path d="M1 1l6 4.5L13 1" fill="none" stroke="#fff" stroke-width="1.2"/></svg></div>
<div class="social" style="left:185px" aria-label="Call"><svg width="14" height="14" viewBox="0 0 24 24"><path d="M5 2l4 4-2 3c1 3 4 6 7 7l3-2 4 4-3 3C10 21 3 14 2 5z" fill="#fff"/></svg></div>
<div class="social" style="left:220px" aria-label="Location"><svg width="12" height="14" viewBox="0 0 20 26"><path d="M10 25S2 14 2 9a8 8 0 0116 0c0 5-8 16-8 16z" fill="#fff"/><circle cx="10" cy="9" r="3" fill="#231f1c"/></svg></div>

<div class="abs footer-col" style="left:557px;top:3302px"><h4>Contact Us</h4></div>
<svg class="abs" style="left:555px;top:3350px" width="20" height="26" viewBox="0 0 20 26"><path d="M10 25S2 14 2 9a8 8 0 0116 0c0 5-8 16-8 16z" fill="none" stroke="#fff" stroke-width="1.3"/><circle cx="10" cy="9" r="3" fill="none" stroke="#fff" stroke-width="1.3"/></svg>
<div class="contact-item" style="top:3345px">Lorem ipsum dolor sit amet,<br>consectetur</div>
<svg class="abs" style="left:555px;top:3398px" width="24" height="24" viewBox="0 0 24 24"><path d="M5 2l4 4-2 3c1 3 4 6 7 7l3-2 4 4-3 3C10 21 3 14 2 5z" fill="none" stroke="#fff" stroke-width="1.3"/></svg>
<div class="contact-item" style="top:3403px">Phone: +1 555 010 2030</div>
<svg class="abs" style="left:555px;top:3446px" width="26" height="18" viewBox="0 0 26 18"><rect x="1" y="1" width="24" height="16" fill="none" stroke="#fff" stroke-width="1.3"/><path d="M1 1l12 9 12-9" fill="none" stroke="#fff" stroke-width="1.3"/></svg>
<div class="contact-item" style="top:3438px">Email<br>hello@tidewellcomforts.com</div>

<div class="abs footer-col" style="left:975px;top:3302px">
  <h4>Our Events</h4>
  <ul><li>Weddings</li><li>Private parties</li><li>Festivals</li><li>Family reunions</li><li>Team building</li></ul>
</div>

<div class="abs footer-rule"></div>
<p class="abs copyright">Copyright 2022 All Rights Reserved. <u>Our Complaints</u> and <u>Feedback Policy</u></p>

</body>
</html>
```